Locksmith Business Cards

My father-in-law is in need of new business cards for his locksmith business and I need to impress him. Kindly help me out!

You can see the previous business card attached. It is a family run business in North Wales.

No individual names on the cards.

Key Things to Feature:
- The words "Prompt", "Local", "Reliable" (as you can see under the logo on the website)
- 24h Emergency Service
- Covering All of North Wales, the Wirral and Chester
- The color blue
- A key or a lock would be interesting (similar to the ones that come up when you google locksmith business card)

Optional (only if design includes bullet points, like the example below):
https://imgvaultcdn.net/samples/208314/55172/55172_3904821_208314_image.jpg
- Residential / Commercial / Automotive
- Alarms & Cameras
- Key Cutting & Safes

https://www.brynhafod-locksmiths.co.uk/

Industry/Entity Type

Locksmith

Contact Information for Business Card

01632 960 418
07700 900 362
brynhafodlocksmiths@mailvane.com
Brynhafod Locksmiths, The Willow Barn, 7 Tannery Rd., Llandudno LL99 4QX
www.brynhafod-locksmiths.co.uk

Requirements
Must have
• - The words "Prompt", "Local", "Reliable" (as you can see under the logo on the website)
• - 24h Emergency Service
• - Covering All of North Wales, the Wirral and Chester
Nice to have
• - A key or a lock would be interesting (similar to the ones that come up when you google locksmith business card)

```html
<!DOCTYPE html>
<html lang="en">
<head>
<meta charset="utf-8">
<title>Brynhafod Locksmiths – Business Cards</title>
<link rel="stylesheet" href="https://fonts.googleapis.com/css2?family=Oswald:wght@500&family=Montserrat:wght@500;600&family=Exo+2:wght@400;500&display=swap">
<style>
  :root {
    --navy: #232a78;
    --navy-deep: #1d2266;
    --band-blue: #4b5aa6;
    --paper: #f3f3f3;
    --white: #ffffff;
    --bullet: #2f9be0;
    --backdrop: #e6e7ec;
  }
  * { box-sizing: border-box; margin: 0; padding: 0; }
  html, body { width: 1200px; height: 1050px; overflow: hidden; }
  body {
    background: var(--backdrop);
    position: relative;
    font-family: "Exo 2", sans-serif;
  }
  .card {
    position: absolute;
    left: 290px;
    width: 620px;
    height: 400px;
    border-radius: 26px;
    overflow: hidden;
  }

  /* Front */
  .card-front { top: 60px; background: var(--navy); color: var(--white); }
  .front-lockup {
    position: absolute; left: 0; right: 0; top: 120px;
    display: flex; flex-direction: column; align-items: center;
  }
  .brand-row { display: flex; align-items: center; gap: 18px; }
  .brand-mark { width: 22px; height: 22px; background: var(--white); }
  .brand-name {
    font-family: "Oswald", sans-serif; font-weight: 500;
    font-size: 50px; line-height: 0.95; letter-spacing: 1px;
    text-transform: uppercase;
  }
  .tagline {
    font-family: "Montserrat", sans-serif; font-weight: 600;
    font-size: 17px; letter-spacing: 3px; margin-top: 22px;
  }
  .tagline .sep { margin: 0 12px; font-weight: 500; }

  /* Back */
  .card-back { top: 560px; background: var(--paper); color: var(--navy); }
  .back-brand {
    position: absolute; left: 36px; top: 48px;
    display: flex; align-items: center; gap: 14px;
  }
  .back-brand .brand-mark { background: var(--navy); width: 20px; height: 20px; }
  .back-brand .brand-name { font-size: 40px; color: var(--navy); }
  .contact-band {
    position: absolute; left: 0; top: 160px; width: 360px; height: 150px;
    background: var(--band-blue); color: var(--white);
    padding: 16px 0 0 36px;
  }
  .contact-list { list-style: none; font-size: 15.5px; line-height: 22px; }
  .contact-list li { display: flex; align-items: center; gap: 12px; }
  .contact-list li.indent { padding-left: 26px; }
  .contact-list svg { width: 14px; height: 14px; flex: none; fill: var(--white); }
  .services {
    position: absolute; left: 336px; top: 112px; right: 0; height: 200px;
    background: var(--navy-deep); color: var(--white);
    border-radius: 22px 0 0 22px;
    padding: 24px 18px 0 26px;
  }
  .services ul { list-style: none; font-size: 15.5px; line-height: 23px; }
  .services li { position: relative; padding-left: 18px; }
  .services li::before {
    content: ""; position: absolute; left: 0; top: 9px;
    width: 6px; height: 6px; border-radius: 50%; background: var(--bullet);
  }
  .services li.cont::before { display: none; }
  .card-back .tagline {
    position: absolute; left: 36px; bottom: 36px; margin: 0;
    font-size: 15px; color: var(--navy);
  }
</style>
</head>
<body>

<section class="card card-front" aria-label="Business card front">
  <div class="front-lockup">
    <div class="brand-row">
      <span class="brand-mark" aria-hidden="true"></span>
      <div class="brand-name">Brynhafod<br>Locksmiths</div>
    </div>
    <p class="tagline">PROMPT<span class="sep">|</span>LOCAL<span class="sep">|</span>RELIABLE</p>
  </div>
</section>

<section class="card card-back" aria-label="Business card back">
  <div class="back-brand">
    <span class="brand-mark" aria-hidden="true"></span>
    <div class="brand-name">Brynhafod<br>Locksmiths</div>
  </div>

  <div class="contact-band">
    <ul class="contact-list">
      <li><svg viewBox="0 0 24 24"><path d="M6.6 10.8a15 15 0 0 0 6.6 6.6l2.2-2.2a1 1 0 0 1 1-.25 11.4 11.4 0 0 0 3.6.57 1 1 0 0 1 1 1V20a1 1 0 0 1-1 1A17 17 0 0 1 3 4a1 1 0 0 1 1-1h3.5a1 1 0 0 1 1 1c0 1.25.2 2.45.57 3.6a1 1 0 0 1-.25 1z"/></svg>01632 960 418</li>
      <li><svg viewBox="0 0 24 24"><path d="M6.6 10.8a15 15 0 0 0 6.6 6.6l2.2-2.2a1 1 0 0 1 1-.25 11.4 11.4 0 0 0 3.6.57 1 1 0 0 1 1 1V20a1 1 0 0 1-1 1A17 17 0 0 1 3 4a1 1 0 0 1 1-1h3.5a1 1 0 0 1 1 1c0 1.25.2 2.45.57 3.6a1 1 0 0 1-.25 1z"/></svg>07700 900 362</li>
      <li><svg viewBox="0 0 24 24"><path d="M2 5h20v14H2z M3 6l9 7 9-7" fill="none" stroke="#fff" stroke-width="2"/></svg>brynhafodlocksmiths@mailvane.com</li>
      <li><svg viewBox="0 0 24 24"><g fill="none" stroke="#fff" stroke-width="2"><circle cx="12" cy="12" r="9"/><path d="M3 12h18M12 3c3 3 3 15 0 18M12 3c-3 3-3 15 0 18"/></g></svg>www.brynhafod-locksmiths.co.uk</li>
      <li><svg viewBox="0 0 24 24"><path d="M12 2a7 7 0 0 0-7 7c0 5 7 13 7 13s7-8 7-13a7 7 0 0 0-7-7zm0 9.5A2.5 2.5 0 1 1 12 6.5a2.5 2.5 0 0 1 0 5z"/></svg>The Willow Barn, 7 Tannery Rd.,</li>
      <li class="indent">Llandudno LL99 4QX</li>
    </ul>
  </div>

  <div class="services">
    <ul>
      <li>24h Emergency Service</li>
      <li>Covering All of North Wales,</li>
      <li class="cont">the Wirral and Chester</li>
      <li>Residential / Commercial / Automotive</li>
      <li>Alarms &amp; Cameras</li>
      <li>Key Cutting &amp; Safes</li>
    </ul>
  </div>

  <p class="tagline">PROMPT<span class="sep">|</span>LOCAL<span class="sep">|</span>RELIABLE</p>
</section>

</body>
</html>
```